Natural healthcare clinic needs stationery and business card design

We have had a logo developed by Pixel Harbor and are now looking at utilising it for a new business concept. The concept is a natural healthcare clinic that hosts a number of small businesses. The individual practitioners may want to utilise the host business stationery to provide a consistent message to clients.

I am looking for a stationery design - letterhead, DL brochure template and business card that uses our logo. The business name 'Bright Meadows' is all about getting rhythm back into your life so you can be fit and healthy. The stationery design should reflect this.

There are a couple of requirements for the business card, it needs to be double-sided with black and white back. There should be lines to write appointment times on. The cards may need to be custom named on the front for example Carol Fenwick, Remedial Therapist and Aromatherapist. Therefore if a template can be provided so we can customise this information using MS Publisher, it would be appreciated.

The DL brochure template needs to be A4 folded to DL. I am looking for a consistent brand message that can be utilised to produce our own clinic brochures.

The natural healthcare clinic will host the following types of businesses - remedial massage, pregnancy massage, oncology massage, aromatherapy, acupuncture - as a bit of a guide.

Target Market(s)

25-45 year old male and females who work full time.

Industry/Entity Type

Healthcare

Requirements
Must have
• Use the logo I have already.

```html
<!DOCTYPE html>
<html lang="en">
<head>
<meta charset="utf-8">
<title>Bright Meadows – Stationery Set</title>
<link href="https://fonts.googleapis.com/css2?family=PT+Sans:wght@400;700&display=swap" rel="stylesheet">
<style>
:root{
  --stage:#4b3526;
  --paper:#ffffff;
  --olive:#7f8d3d;
  --olive-dark:#5d6829;
  --leaf:#8db83a;
  --leaf-light:#a8cc4e;
  --ink:#3d3d3d;
  --muted:#6d6d6d;
  --red:#e1261c;
  --navy:#2b3990;
  --grey-top:#f4f4f4;
  --grey-bottom:#cfcfcf;
  --label:#ffffff;
}
*{box-sizing:border-box;margin:0;padding:0}
html,body{width:1200px;height:675px;overflow:hidden;background:var(--stage)}
body{font-family:"PT Sans",Arial,sans-serif;color:var(--ink)}
.canvas{position:relative;width:1200px;height:675px;background:var(--stage)}
.label{position:absolute;color:var(--label);font-weight:700;font-size:15px;letter-spacing:.2px}
.sheet{position:absolute;background:var(--paper);box-shadow:0 3px 10px rgba(0,0,0,.45);overflow:hidden}
.photo{position:absolute;border-radius:4px}
.brand{display:flex;align-items:center;gap:5px;font-weight:400;color:var(--olive)}
.brand .dot{border-radius:50%;background:var(--leaf);flex:none}
.brand-sub{color:var(--muted);font-size:7px}
.copy{font-size:5.2px;line-height:1.45;color:var(--ink)}
.copy.light{color:#fff}
.tab{position:relative;background:linear-gradient(90deg,var(--leaf),var(--leaf-light));color:#fff;font-weight:700;font-size:8.5px;padding:3px 10px;width:92px;clip-path:polygon(0 0,90% 0,100% 50%,90% 100%,0 100%);margin-left:-12px}
.green-bar{background:linear-gradient(90deg,var(--leaf),var(--olive));color:#fff}

/* Letterhead */
.letterhead{left:58px;top:54px;width:361px;height:468px}
.letterhead .brand{position:absolute;left:26px;top:68px;font-size:13px}
.letterhead .brand .dot{width:10px;height:10px}
.letterhead .brand-sub{position:absolute;left:26px;top:86px;font-size:5.5px}
.letterhead .watermark{position:absolute;left:40px;top:300px;width:200px;height:150px;border-radius:50%;background:radial-gradient(circle,rgba(141,184,58,.16),rgba(141,184,58,0) 70%)}
.letterhead .footer{position:absolute;left:0;bottom:0;width:100%;height:16px;display:flex}
.letterhead .footer .contact{flex:0 0 70%;display:flex;align-items:center;gap:10px;padding-left:10px;font-size:5.5px;clip-path:polygon(0 0,100% 0,93% 100%,0 100%)}
.letterhead .footer .address{flex:1;background:var(--olive-dark);color:#fff;font-size:5.5px;display:flex;align-items:center;padding-left:4px;margin-left:-14px}
.icon{display:inline-block;width:6px;height:6px;border-radius:50%;background:#fff;margin-right:2px;vertical-align:middle}

/* Business cards */
.card{top:548px;width:150px;height:84px}
.card-front{left:58px}
.card-back{left:218px}
.card .brand{position:absolute;left:10px;top:42px;font-size:9px}
.card .brand .dot{width:6px;height:6px}
.card .card-sub{position:absolute;left:10px;top:55px;font-size:4.5px;color:var(--muted)}
.card .person{position:absolute;left:105px;top:8px;font-size:6px;font-weight:700;color:var(--ink)}
.card .role{position:absolute;left:105px;top:16px;font-size:3.8px;line-height:1.3;color:var(--olive)}
.card .addr{position:absolute;left:105px;top:42px;font-size:3.6px;line-height:1.3;color:var(--muted)}
.card .strip{position:absolute;left:0;bottom:0;width:100%;height:11px;display:flex;align-items:center;font-size:3.8px;padding:0 6px;justify-content:space-between}
.card .strip .phone{font-size:5px}
.card-back .lines{position:absolute;left:62px;top:22px;width:80px}
.card-back .lines span{display:block;height:8px;border-bottom:.6px solid var(--leaf)}
.card-back .addr{left:62px;top:60px}
.card-back .strip{background:linear-gradient(90deg,var(--olive-dark) 0 42%,var(--leaf) 42%);font-size:5px}
.card-back .strip b{font-weight:700;font-size:6px}

/* Brochure sheets */
.brochure{top:54px;width:351px;height:496px;display:flex}
.brochure-outside{left:441px}
.brochure-inside{left:805px}
.panel{position:relative;width:50%;height:100%;overflow:hidden}
.panel-olive{background:var(--olive);color:#fff}
.panel-grey{background:linear-gradient(180deg,var(--grey-top),var(--grey-bottom))}
.panel-title{font-size:11px;font-weight:400;line-height:1.35;color:#fff}

/* Outside back panel */
.back-panel .photo{left:0;top:0;width:175px;height:108px;border-radius:0;background:linear-gradient(135deg,#e9cdb4,#c98f74 55%,#8c2b2b)}
.back-panel .intro{position:absolute;left:12px;top:130px}
.back-panel .sections{position:absolute;left:12px;top:178px;width:155px}
.back-panel .section{margin-bottom:9px}
.back-panel .section .copy{margin-top:5px}
.back-panel .big-phone{position:absolute;left:12px;top:416px;font-size:15px;color:#fff}
.back-panel .foot{position:absolute;left:0;bottom:0;width:100%;height:62px;background:linear-gradient(180deg,#f0f0f0,#d3d3d3)}
.back-panel .foot .mini{position:absolute;left:0;top:6px;width:85px;height:48px;background:#fff;clip-path:polygon(0 0,100% 0,80% 100%,0 100%)}
.back-panel .foot .brand{position:absolute;left:12px;top:22px;font-size:9px}
.back-panel .foot .brand .dot{width:6px;height:6px}
.back-panel .foot .brand-sub{position:absolute;left:12px;top:36px;font-size:5px}
.back-panel .foot .addr{position:absolute;left:104px;top:14px;font-size:5px;line-height:1.35;color:var(--ink)}

/* Outside front panel */
.front-panel .top-stripe{position:absolute;left:0;top:0;width:100%;height:14px;background:linear-gradient(90deg,var(--leaf),var(--olive));clip-path:polygon(0 0,100% 0,100% 100%,0 60%)}
.front-panel .headline{position:absolute;left:0;top:20px;width:100%;text-align:center;color:var(--red);font-weight:700;font-size:14px;line-height:1.1}
.front-panel .services{position:absolute;left:8px;top:58px;width:160px;text-align:center;color:var(--navy);font-weight:700;font-size:8.5px;line-height:1.35}
.front-panel .brand{position:absolute;left:15px;top:196px;font-size:17px}
.front-panel .brand .dot{width:11px;height:11px}
.front-panel .brand-sub{position:absolute;left:17px;top:218px;font-size:7px}
.front-panel .intro{position:absolute;left:12px;top:240px;width:155px}
.front-panel .photo-a{left:12px;top:282px;width:156px;height:92px;background:linear-gradient(135deg,#f2c48d,#d98a4a 60%,#b86b32)}
.front-panel .photo-b{left:12px;top:382px;width:156px;height:92px;background:linear-gradient(135deg,#f1e2d4,#d4a589 50%,#8f5b41)}
.front-panel .bottom{position:absolute;left:0;bottom:0;width:100%;height:34px;padding:4px 12px}
.front-panel .bottom .phone{font-size:11px;font-weight:700}
.front-panel .bottom .web{font-size:6px;letter-spacing:1px;font-weight:700}

/* Inside front panel */
.inside-front .photo{left:0;top:12px;width:175px;height:210px;border-radius:0;background:linear-gradient(160deg,#ffffff 0 30%,#e8d6cc 45%,#c9a493 60%,#9b8bb0 85%,#6f5c8c)}
.inside-front .brand{position:absolute;left:18px;top:300px;font-size:17px}
.inside-front .brand .dot{width:11px;height:11px}
.inside-front .brand-sub{position:absolute;left:20px;top:322px;font-size:7px}
.inside-front .message{position:absolute;left:0;top:346px;width:100%;text-align:center;color:var(--olive);font-size:12px}
.inside-front .copy-block{position:absolute;left:12px;top:370px;width:155px}
.inside-front .copy-block .copy{margin-bottom:6px}
.inside-front .top-stripe{position:absolute;left:0;top:0;width:100%;height:12px;background:linear-gradient(90deg,var(--leaf),var(--olive))}

/* Inside back panel */
.inside-back .top-stripe{position:absolute;left:0;top:0;width:100%;height:12px;background:var(--olive-dark)}
.inside-back .title{position:absolute;left:12px;top:30px}
.inside-back .photo-a{left:12px;top:76px;width:155px;height:88px;background:linear-gradient(135deg,#e8b99a,#b8542e 55%,#6b1d12)}
.inside-back .intro{position:absolute;left:12px;top:176px;width:155px}
.inside-back .sections{position:absolute;left:12px;top:222px;width:155px}
.inside-back .section{margin-bottom:8px}
.inside-back .section .copy{margin-top:5px}
.inside-back .photo-b{left:12px;top:370px;width:155px;height:88px;background:linear-gradient(135deg,#f4f1ee,#dcc6b6 50%,#a98a78)}
.inside-back .more{position:absolute;left:0;top:466px;width:100%;text-align:center;font-size:6px}
.inside-back .phone{position:absolute;left:0;top:474px;width:100%;text-align:center;font-size:15px}
.inside-back .web{position:absolute;left:0;top:493px;width:100%;text-align:center;font-size:6px;letter-spacing:1.2px;font-weight:700}
</style>
</head>
<body>
<div class="canvas">

  <div class="label" style="left:58px;top:24px">Letterhead option 5</div>
  <div class="label" style="left:443px;top:28px">Back</div>
  <div class="label" style="left:746px;top:28px">Front</div>
  <div class="label" style="left:808px;top:28px">Front Inside</div>
  <div class="label" style="left:1072px;top:32px">Back Inside</div>

  <!-- Letterhead -->
  <section class="sheet letterhead" aria-label="Letterhead">
    <div class="brand"><span class="dot"></span>Bright Meadows</div>
    <div class="brand-sub">Well Being Clinic</div>
    <div class="watermark"></div>
    <div class="footer">
      <div class="contact green-bar">
        <span><i class="icon"></i>012.345.6789</span>
        <span><i class="icon"></i>info@brightmeadows.com</span>
        <span><i class="icon"></i>www.brightmeadows.com</span>
      </div>
      <div class="address">Suite 000, City name, Country name 00000</div>
    </div>
  </section>

  <!-- Business card front -->
  <section class="sheet card card-front" aria-label="Business card front">
    <div class="person">CAROL FENWICK</div>
    <div class="role">Remedial Therapist &amp;<br>Aromatherapist</div>
    <div class="addr">Suite 000, City name<br>Country name 00000</div>
    <div class="brand"><span class="dot"></span>Bright Meadows</div>
    <div class="card-sub">Well Being Clinic</div>
    <div class="strip green-bar">
      <span>info@brightmeadows.com<br>www.brightmeadows.com</span>
      <span class="phone">012.345.6789</span>
    </div>
  </section>

  <!-- Business card back -->
  <section class="sheet card card-back" aria-label="Business card back">
    <div class="lines"><span></span><span></span><span></span><span></span></div>
    <div class="addr">Suite 000, City name, Country name</div>
    <div class="strip" style="color:#fff">
      <span>Well Being Clinic</span>
      <b>Appointment</b>
    </div>
  </section>

  <!-- Brochure outside -->
  <section class="sheet brochure brochure-outside" aria-label="Brochure outside">
    <div class="panel panel-olive back-panel">
      <div class="photo" role="img" aria-label="Photo of a client relaxing during a back massage"></div>
      <h2 class="panel-title intro">Lorem Ipsum Dolor sit<br>Consectetur adipisicing</h2>
      <div class="sections">
        <div class="section">
          <div class="tab">Remedial Massage</div>
          <p class="copy light">Lorem ipsum dolor sit amet, consectetur adipisicing elit, sed do eiusmod tempor incididunt ut labore et dolore magna aliqua. Ut enim ad minim veniam, quis nostrud exercitation ullamco laboris nisi ut aliquip ex ea commodo consequat. Duis aute irure dolor in reprehenderit in voluptate velit esse cillum dolore eu fugiat nulla pariatur.</p>
        </div>
        <div class="section">
          <div class="tab">Pregnancy Massage</div>
          <p class="copy light">Lorem ipsum dolor sit amet, consectetur adipisicing elit, sed do eiusmod tempor incididunt ut labore et dolore magna aliqua. Ut enim ad minim veniam, quis nostrud exercitation ullamco laboris nisi ut aliquip ex ea commodo consequat. Duis aute irure dolor in reprehenderit in voluptate velit esse cillum dolore eu fugiat nulla pariatur. Excepteur sint occaecat cupidatat non proident.</p>
        </div>
        <div class="section">
          <div class="tab">Oncology Massage</div>
          <p class="copy light">Lorem ipsum dolor sit amet, consectetur adipisicing elit, sed do eiusmod tempor incididunt ut labore et dolore magna aliqua. Ut enim ad minim veniam, quis nostrud exercitation ullamco laboris nisi ut aliquip ex ea commodo consequat. Duis aute irure dolor in reprehenderit in voluptate velit esse cillum dolore eu fugiat nulla pariatur. Excepteur sint occaecat cupidatat non proident, sunt in culpa qui officia deserunt mollit anim id est laborum.</p>
        </div>
      </div>
      <div class="big-phone">012.345.6789</div>
      <div class="foot">
        <div class="mini"></div>
        <div class="brand"><span class="dot"></span>Bright Meadows</div>
        <div class="brand-sub">Well Being Clinic</div>
        <div class="addr">Suite 000, City name<br>Country name 00000<br><br>info@brightmeadows.com<br>www.brightmeadows.com</div>
      </div>
    </div>

    <div class="panel panel-grey front-panel">
      <div class="top-stripe"></div>
      <h1 class="headline">Lorem<br>Ipsum Dolor sit</h1>
      <p class="services">Remedial Massage<br>Pregnancy Massage, Oncology Massage, Aromatherapy, Acupuncture</p>
      <div class="brand"><span class="dot"></span>Bright Meadows</div>
      <div class="brand-sub">Well Being Clinic</div>
      <p class="copy intro">Lorem ipsum dolor sit amet, consectetur adipisicing elit, sed do eiusmod tempor incididunt ut labore et dolore magna aliqua. Ut enim ad minim veniam, quis nostrud exercitation ullamco laboris nisi.</p>
      <div class="photo photo-a" role="img" aria-label="Close-up photo of hands massaging a back"></div>
      <div class="photo photo-b" role="img" aria-label="Photo of a client receiving a shoulder massage"></div>
      <div class="bottom green-bar">
        <div class="phone">012.345.6789</div>
        <div class="web">www.brightmeadows.com</div>
      </div>
    </div>
  </section>

  <!-- Brochure inside -->
  <section class="sheet brochure brochure-inside" aria-label="Brochure inside">
    <div class="panel panel-grey inside-front">
      <div class="top-stripe"></div>
      <div class="photo" role="img" aria-label="Spa photo of a relaxed client with massage stones and lavender salts"></div>
      <div class="brand"><span class="dot"></span>Bright Meadows</div>
      <div class="brand-sub">Well Being Clinic</div>
      <h2 class="message">BRAND MESSAGE</h2>
      <div class="copy-block">
        <p class="copy">Lorem ipsum dolor sit amet, consectetur adipisicing elit, sed do eiusmod tempor incididunt ut labore et dolore magna aliqua. Ut enim ad minim veniam, quis nostrud exercitation ullamco laboris nisi ut aliquip ex ea commodo consequat. Duis aute irure dolor in reprehenderit in voluptate velit esse cillum dolore eu fugiat nulla pariatur. Lorem ipsum dolor sit amet, consectetur adipisicing elit, sed do eiusmod tempor incididunt ut labore et dolore magna aliqua. Ut enim ad minim veniam, quis nostrud exercitation ullamco laboris nisi ut aliquip ex ea commodo consequat. Duis aute irure dolor in reprehenderit in voluptate velit esse cillum dolore eu fugiat nulla pariatur.</p>
        <p class="copy">Lorem ipsum dolor sit amet, consectetur adipisicing elit, sed do eiusmod tempor incididunt ut labore et dolore magna aliqua. Ut enim ad minim veniam, quis nostrud exercitation ullamco laboris nisi ut aliquip ex ea commodo consequat. Duis aute irure dolor in reprehenderit in voluptate velit esse cillum dolore eu fugiat nulla pariatur.</p>
      </div>
    </div>

    <div class="panel panel-olive inside-back">
      <div class="top-stripe"></div>
      <h2 class="panel-title title">Lorem Ipsum Dolor sit<br>Consectetur adipisicing</h2>
      <div class="photo photo-a" role="img" aria-label="Photo of a hot stone massage with rose petals"></div>
      <p class="copy light intro">Lorem ipsum dolor sit amet, consectetur adipisicing elit, sed do eiusmod tempor incididunt ut labore et dolore magna aliqua. Ut enim ad minim veniam, quis nostrud exercitation ullamco laboris nisi.</p>
      <div class="sections">
        <div class="section">
          <div class="tab">Aromatherapy</div>
          <p class="copy light">Lorem ipsum dolor sit amet, consectetur adipisicing elit, sed do eiusmod tempor incididunt ut labore et dolore magna aliqua. Ut enim ad minim veniam, quis nostrud exercitation ullamco laboris nisi ut aliquip ex ea commodo consequat. Duis aute irure dolor in reprehenderit in voluptate velit esse cillum dolore eu fugiat nulla pariatur. Excepteur sint occaecat cupidatat non proident.</p>
        </div>
        <div class="section">
          <div class="tab">Acupuncture</div>
          <p class="copy light">Lorem ipsum dolor sit amet, consectetur adipisicing elit, sed do eiusmod tempor incididunt ut labore et dolore magna aliqua. Ut enim ad minim veniam, quis nostrud exercitation ullamco laboris nisi ut aliquip ex ea commodo consequat. Duis aute irure dolor in reprehenderit in voluptate velit esse cillum dolore eu fugiat nulla pariatur. Excepteur sint occaecat cupidatat non proident.</p>
        </div>
      </div>
      <div class="photo photo-b" role="img" aria-label="Photo of an acupuncture treatment on a relaxed client"></div>
      <div class="more">For more information</div>
      <div class="phone">012.345.6789</div>
    </div>
  </section>

  <div class="label" style="left:980px;top:544px;font-size:6px;letter-spacing:1.2px;width:175px;text-align:center">www.brightmeadows.com</div>

</div>
</body>
</html>
```